Bespoke Builders Business Card Design

We need a business card for an established builder of high quality bespoke homes in Auckland and Northland. We build and renovate homes collaboratively facilitating effective communication between owners, builders, architects, suppliers and tradespeople. We have never built or renovated a home that leaks or has faults. We only use reliable materials. We have never been sued or had legal action taken against us. We are honest builders of bespoke homes not group mass produced homes. Our niche market is in character homes. We practice sustainability and have built a lot of coastal property. We have been in business for over thirty years . We would like to see natural colors of the environment sand,sea and maybe vegetation . The design should communicate quality, sustainability,fair pricing, open communication and the originality of bespoke building. And the fact that the builder is registered.

Industry/Entity Type

Business

Contact Information for Business Card

Rowan Tellick Builders
Ph. 021583917
18 Kestrel Rd Harwood Bay Auckland 0814
PO Box 927 Mangawhai 0583

```html
<!DOCTYPE html>
<html lang="en">
<head>
<meta charset="utf-8">
<title>Rowan Tellick Builders — Business Card</title>
<link rel="stylesheet" href="https://fonts.googleapis.com/css2?family=Tinos:wght@400;700&display=swap">
<style>
  :root {
    --page: #e9e6e0;
    --sand-light: #fbf7ee;
    --sand: #efe4cc;
    --ink: #22301f;
    --sea: #2e7d86;
    --bush: #22402e;
    --on-dark: #f8f3e6;
  }
  * { box-sizing: border-box; margin: 0; padding: 0; }
  html, body {
    width: 1189px;
    height: 1200px;
    overflow: hidden;
    background: var(--page);
    font-family: "Tinos", "Times New Roman", serif;
  }
  .canvas {
    position: relative;
    width: 1189px;
    height: 1200px;
  }
  .card {
    position: absolute;
    left: 140px;
    width: 917px;
    height: 524px;
    overflow: hidden;
    box-shadow: 0 4px 10px rgba(0,0,0,0.18);
  }
  .card--front { top: 45px; background: var(--sand-light); }
  .card--back {
    top: 624px;
    background: var(--sand-light);
    border: 25px solid var(--sea);
  }
  .wave {
    position: absolute;
    inset: 0;
    width: 100%;
    height: 100%;
  }
  .wave__band { fill: var(--sea); }
  .wave__base { fill: var(--bush); }
  .company-name {
    position: absolute;
    left: 0;
    right: 0;
    text-align: center;
    font-weight: 700;
    color: var(--ink);
    letter-spacing: 0.5px;
    white-space: nowrap;
  }
  .card--front .company-name { top: 122px; font-size: 58px; line-height: 1; }
  .card--back .company-name { top: 206px; font-size: 65px; line-height: 1; }
  .contact {
    position: absolute;
    right: 131px;
    top: 354px;
    text-align: right;
    color: var(--on-dark);
    font-size: 29px;
    line-height: 40px;
  }
  .contact__line { white-space: nowrap; }
  .icon {
    position: absolute;
    left: 807px;
    width: 23px;
    height: 23px;
  }
  .icon--phone { top: 363px; }
  .icon--pin { top: 403px; }
  .icon__tile { fill: var(--on-dark); }
  .icon__mark { fill: var(--bush); }
</style>
</head>
<body>
<main class="canvas">
  <section class="card card--front" aria-label="Front of business card">
    <svg class="wave" viewBox="0 0 1124 642" preserveAspectRatio="none" aria-hidden="true">
      <path class="wave__band" d="M0,377 C240,445 450,440 650,392 C790,358 900,330 990,330 C1060,332 1095,375 1124,423 L1124,642 L0,642 Z"/>
      <path class="wave__base" d="M0,440 C170,480 370,482 580,430 C740,390 860,350 960,342 C1045,340 1095,395 1124,423 L1124,642 L0,642 Z"/>
    </svg>
    <h1 class="company-name">Rowan Tellick Builders</h1>
    <div class="contact">
      <p class="contact__line">021583917</p>
      <p class="contact__line">18 Kestrel Rd Harwood Bay</p>
      <p class="contact__line">Auckland 0814 PO Box 927 Mangawhai 0583</p>
    </div>
    <svg class="icon icon--phone" viewBox="0 0 24 24" aria-hidden="true">
      <rect class="icon__tile" x="0" y="0" width="24" height="24" rx="2"/>
      <rect class="icon__mark" x="7" y="4" width="10" height="16" rx="1.5"/>
      <rect class="icon__tile" x="8.5" y="6" width="7" height="4"/>
      <rect x="8.5" y="12" width="7" height="6" fill="#7f9a86"/>
    </svg>
    <svg class="icon icon--pin" viewBox="0 0 24 24" aria-hidden="true">
      <rect class="icon__tile" x="0" y="0" width="24" height="24" rx="2"/>
      <path class="icon__mark" d="M12 4 C8.7 4 6.5 6.4 6.5 9.3 C6.5 13 12 20 12 20 C12 20 17.5 13 17.5 9.3 C17.5 6.4 15.3 4 12 4 Z"/>
      <circle class="icon__tile" cx="12" cy="9.3" r="2.2"/>
    </svg>
  </section>

  <section class="card card--back" aria-label="Back of business card">
    <h2 class="company-name">Rowan Tellick Builders</h2>
  </section>
</main>
</body>
</html>
```